Atelier Quai Sept (Masterclasses for Actors) needs artistic and modern website in French & English

Hello!

We need to create a new website (existing : www.lune-rouge-studio.example) for our acting school that holds Masterclasses for professional actors in Paris. It needs to be in French and English with an easy to use back office (wordpress is slow and complicated) (ideas?) so we can add or change workshop dates, upload new photos or videos to the gallery ourselves and make basic changes to the information on line.

Our main clients are French but we have international guests coming who only understand english.

Ideally you would know how to link your creation to the existing domain name, how to make sure the email adresses remain the same and help us find the least expensive but best all in 1 proposition to make it as easy as possible to pay the yearly fee to the hosting platform / web name / etc :-)

Design wise we would like something creative, linked to films etc but without using to many clichés. The logo and a stamp have already been created and we would like to keep these (which has the colours we would like you to use).

It would be nice to maybe have a moving image when you first open the page, maybe the logo itself, something dynamic and visual...

Thank you for you time in reading this!

Margot & Ninon & Apolline
Team LRS

Target Market(s)

actors

Coding

Coded - Design and coding required

Number of Pages Required

5+ page

Font styles to use
Sans Serif

Colors
34a7d8

Requirements
Must have
• able to be read on all electronic devices
Nice to have
• some fun and humour / class
Should not have
• too corporate

```html
<!DOCTYPE html>
<html lang="en">
<head>
<meta charset="utf-8">
<title>Atelier Quai Sept — Masterclasses for Actors</title>
<link rel="stylesheet" href="https://fonts.googleapis.com/css2?family=Montserrat:wght@400;600;700&family=Arimo:wght@400;700&display=swap">
<style>
  :root {
    --blue: #2f8bd3;
    --ink: #333333;
    --grey: #6b6b6b;
    --grey-light: #999999;
    --icon-grey: #6e6e6e;
    --rule: #e3e3e3;
    --paper: #ffffff;
    --paper-soft: #f6f6f6;
    --star: #e7b521;
  }
  * { margin: 0; padding: 0; box-sizing: border-box; }
  html, body { width: 1200px; height: 3087px; overflow: hidden; background: var(--paper); }
  body { font-family: "Arimo", Arial, sans-serif; color: var(--ink); }
  section, header, footer, nav { position: relative; width: 1200px; }
  .abs { position: absolute; }
  .center-x { transform: translateX(-50%); }

  /* Header */
  .site-header { height: 99px; background: var(--paper); }
  .brand { left: 84px; top: 36px; display: flex; align-items: center; gap: 10px; }
  .brand-mark { width: 16px; height: 16px; border-radius: 50%; background: var(--blue); }
  .brand-name { font-family: "Montserrat", sans-serif; font-weight: 600; font-size: 22px; color: var(--grey); letter-spacing: 0.5px; }
  .call { left: 688px; top: 25px; display: flex; align-items: center; gap: 14px; font-size: 15px; color: var(--grey); }
  .call-icon { width: 46px; height: 46px; border: 2px solid var(--blue); border-radius: 50%; display: flex; align-items: center; justify-content: center; }
  .lang { left: 963px; top: 27px; width: 150px; height: 44px; border: 1px solid #d6d6d6; border-radius: 4px; display: flex; align-items: center; padding: 0 12px; gap: 10px; font-size: 12px; color: var(--ink); background: #fafafa; }
  .lang-flag { width: 18px; height: 12px; background: #c9ced8; }
  .lang-caret { margin-left: auto; }

  .main-nav { height: 55px; background: var(--blue); }
  .main-nav a { position: absolute; top: 20px; transform: translateX(-50%); font-family: "Montserrat", sans-serif; font-weight: 700; font-size: 12.5px; color: #fff; text-decoration: none; letter-spacing: 0.3px; white-space: nowrap; }

  /* Hero */
  .hero { height: 490px; overflow: hidden; }
  .hero-photo { position: absolute; inset: 0; background: linear-gradient(180deg, #3f5a2a 0%, #5f7f3c 35%, #7fa552 60%, #8eb35c 100%); }
  .hero-title { left: 600px; top: 302px; font-family: "Montserrat", sans-serif; font-weight: 700; font-size: 44px; color: #fff; letter-spacing: 1px; white-space: nowrap; }
  .hero-sub { left: 600px; top: 364px; width: 610px; text-align: center; font-size: 13px; line-height: 23px; color: #fff; }
  .hero-dots { left: 600px; top: 456px; display: flex; gap: 6px; }
  .hero-dots span { width: 14px; height: 14px; border: 2px solid #fff; border-radius: 50%; }
  .hero-dots span.on { background: #fff; }
  .hero-arrow { right: 18px; top: 36px; }

  /* Welcome */
  .welcome { height: 482px; background: var(--paper); }
  .section-title { font-family: "Montserrat", sans-serif; font-weight: 700; font-size: 23px; color: var(--blue); white-space: nowrap; letter-spacing: 0.3px; }
  .lead { text-align: center; font-size: 12px; line-height: 25px; color: var(--grey); }
  .feature { width: 300px; text-align: center; }
  .feature-icon { width: 116px; height: 116px; border-radius: 50%; background: var(--icon-grey); margin: 0 auto; display: flex; align-items: center; justify-content: center; border: 4px solid #fff; box-shadow: 0 0 0 2px var(--icon-grey); }
  .feature-icon.is-active { background: var(--blue); box-shadow: 0 0 0 2px var(--blue); }
  .feature h3 { margin-top: 20px; font-family: "Montserrat", sans-serif; font-weight: 600; font-size: 16px; color: var(--ink); letter-spacing: 0.5px; }
  .feature h3.is-active { color: var(--blue); }
  .feature p { margin-top: 12px; font-size: 11.5px; line-height: 24px; color: var(--grey); padding: 0 14px; }

  /* Featured video */
  .featured { height: 395px; background: var(--blue); }
  .featured-copy { left: 95px; top: 44px; width: 500px; color: #fff; }
  .featured-copy h2 { font-family: "Montserrat", sans-serif; font-weight: 700; font-size: 22px; letter-spacing: 0.3px; }
  .featured-copy p { margin-top: 16px; font-size: 11.5px; line-height: 23px; }
  .btn-outline { left: 95px; top: 311px; width: 136px; height: 42px; border: 2px solid #fff; color: #fff; font-family: "Montserrat", sans-serif; font-weight: 600; font-size: 13px; display: flex; align-items: center; justify-content: center; }
  .video-still { left: 630px; top: 0; width: 570px; height: 395px; background: linear-gradient(160deg, #6e5a44 0%, #8c7358 40%, #a58c6f 70%, #7c6650 100%); }
  .play { left: 874px; top: 158px; width: 80px; height: 80px; border: 4px solid #fff; border-radius: 50%; display: flex; align-items: center; justify-content: center; }

  /* Gallery */
  .gallery { height: 634px; background: var(--paper); }
  .filters { left: 319px; top: 82px; width: 562px; height: 50px; border: 1px solid var(--rule); display: flex; align-items: center; justify-content: center; gap: 30px; font-family: "Montserrat", sans-serif; font-size: 11px; font-weight: 600; color: var(--grey); }
  .filters .on { color: var(--blue); }
  .filters .sep { color: #bbb; font-weight: 400; }
  .tile { position: absolute; }
  .tile-stages { background: var(--blue); border: 4px solid rgba(255,255,255,0.4); outline: 2px solid #fff; outline-offset: -14px; color: #fff; text-align: center; padding: 36px 28px 0; }
  .tile-stages h4 { font-family: "Montserrat", sans-serif; font-weight: 700; font-size: 22px; letter-spacing: 0.5px; }
  .tile-stages p { margin-top: 10px; font-size: 11.5px; line-height: 23px; }
  .tile-stages .zoom { margin: 12px auto 0; width: 26px; height: 26px; border-radius: 50%; background: #fff; display: flex; align-items: center; justify-content: center; }

  /* Testimonial */
  .testimonial { height: 420px; background: linear-gradient(180deg, #3a3128 0%, #2b2621 50%, #3b3327 100%); color: #fff; }
  .testimonial h2 { left: 600px; top: 80px; font-family: "Montserrat", sans-serif; font-weight: 700; font-size: 23px; color: #fff; white-space: nowrap; }
  .quote-badge { left: 565px; top: 132px; width: 70px; height: 70px; border-radius: 50%; background: #fff; display: flex; align-items: center; justify-content: center; }
  .quote-text { left: 600px; top: 218px; width: 900px; text-align: center; font-size: 12px; line-height: 31px; }
  .stars { left: 600px; top: 318px; display: flex; gap: 3px; }
  .quote-name { left: 600px; top: 344px; font-size: 13.5px; white-space: nowrap; }
  .chev { top: 172px; }

  /* Contact */
  .contact { height: 446px; background: var(--paper-soft); }
  .map { left: 84px; top: 144px; width: 498px; height: 257px; background: linear-gradient(135deg, #e8e4d8 0%, #dcd8c8 45%, #c9d9e6 55%, #e6e2d4 100%); border: 1px solid #d8d8d8; }
  .contact-copy { left: 622px; top: 144px; width: 500px; font-size: 12px; line-height: 24px; color: var(--grey); }
  .contact-label { font-family: "Montserrat", sans-serif; font-weight: 700; font-size: 14px; color: var(--blue); letter-spacing: 0.5px; }
  .contact-detail { font-size: 12px; line-height: 21px; color: var(--grey-light); white-space: nowrap; }
  .socials { left: 870px; top: 360px; display: flex; gap: 9px; }
  .socials span { width: 36px; height: 36px; border: 1.5px solid #a9a9a9; border-radius: 50%; }

  .site-footer { height: 66px; background: var(--blue); color: #fff; font-size: 12px; }
  .site-footer .copy { left: 600px; top: 25px; white-space: nowrap; }
  .site-footer .code { right: 24px; top: 26px; font-size: 11px; }
</style>
</head>
<body>

<header class="site-header">
  <div class="brand abs"><span class="brand-mark"></span><span class="brand-name">Atelier Quai Sept</span></div>
  <div class="call abs">
    <span class="call-icon">
      <svg width="20" height="20" viewBox="0 0 24 24"><path d="M6.6 10.8a15 15 0 0 0 6.6 6.6l2.2-2.2c.3-.3.7-.4 1-.2 1.1.4 2.3.6 3.6.6.6 0 1 .4 1 1V20c0 .6-.4 1-1 1A17 17 0 0 1 3 4c0-.6.4-1 1-1h3.5c.6 0 1 .4 1 1 0 1.3.2 2.5.6 3.6.1.3 0 .7-.2 1z" fill="none" stroke="#2f8bd3" stroke-width="1.8"/></svg>
    </span>
    <span>Call Us : +33 6 12 48 30 57</span>
  </div>
  <div class="lang abs"><span class="lang-flag"></span><span>English</span>
    <svg class="lang-caret" width="10" height="6" viewBox="0 0 10 6"><path d="M1 1l4 4 4-4" fill="none" stroke="#555" stroke-width="1.5"/></svg>
  </div>
</header>

<nav class="main-nav">
  <a style="left:150px">HOME</a>
  <a style="left:249px">ABOUT</a>
  <a style="left:370px">INTERNSHIPS</a>
  <a style="left:494px">PHOTO</a>
  <a style="left:599px">VIDEOS</a>
  <a style="left:704px">EVENTS</a>
  <a style="left:819px">THE TEAM</a>
  <a style="left:945px">PARTNERS</a>
  <a style="left:1052px">BLOG</a>
</nav>

<section class="hero">
  <div class="hero-photo" role="img" aria-label="Photo of actors seated in a circle on a park lawn during an outdoor workshop"></div>
  <svg class="hero-arrow abs" width="22" height="22" viewBox="0 0 22 22"><path d="M6 16L16 6M8 6h8v8" fill="none" stroke="#fff" stroke-width="2"/></svg>
  <div class="hero-title abs center-x">ATELIER QUAI SEPT</div>
  <p class="hero-sub abs center-x">Go a week with us for an internship intensive within a framework of holidays. A total immersion in the evenings and dance shoot and PRO images for your demo tape</p>
  <div class="hero-dots abs center-x"><span class="on"></span><span></span><span></span><span></span><span></span></div>
</section>

<section class="welcome">
  <h2 class="section-title abs center-x" style="left:600px;top:46px">WELCOME TO ATELIER QUAI SEPT</h2>
  <p class="lead abs center-x" style="left:600px;top:90px;width:700px">Go a week with us for an internship intensive within a framework of holidays. A total immersion in the work of actor mixing fun: games, meals, musical evenings and dance shoot and PRO images for your demo tape.</p>

  <div class="feature abs" style="left:105px;top:183px">
    <div class="feature-icon">
      <svg width="56" height="56" viewBox="0 0 56 56" fill="none" stroke="#fff" stroke-width="3">
        <path d="M28 14a12 12 0 0 0-7 22v5h14v-5a12 12 0 0 0-7-22z"/><path d="M23 45h10M24 49h8"/>
        <path d="M28 3v5M10 10l4 4M46 10l-4 4M4 27h5M47 27h5"/>
      </svg>
    </div>
    <h3>CREATIVE</h3>
    <p>Go a week with us for an internship intensive within a framework of holidays. A total immersion in the meals, musical evenings and dance</p>
  </div>
  <div class="feature abs" style="left:451px;top:183px">
    <div class="feature-icon is-active">
      <svg width="58" height="58" viewBox="0 0 58 58" fill="#fff">
        <circle cx="18" cy="17" r="9"/><circle cx="38" cy="15" r="7"/>
        <rect x="10" y="28" width="30" height="20" rx="2"/><path d="M40 34l10-6v20l-10-6z"/>
      </svg>
    </div>
    <h3 class="is-active">CINEMA</h3>
    <p>Go a week with us for an internship intensive within a framework of holidays. A total immersion in the meals, musical evenings and dance</p>
  </div>
  <div class="feature abs" style="left:797px;top:183px">
    <div class="feature-icon">
      <svg width="58" height="58" viewBox="0 0 58 58" fill="none" stroke="#fff" stroke-width="3">
        <rect x="14" y="8" width="38" height="30"/><path d="M24 30l8-8 6 5 8-10"/>
        <circle cx="9" cy="24" r="4" fill="#fff"/><path d="M5 50V34h10l6-6M11 50V40"/>
      </svg>
    </div>
    <h3>TRAINING</h3>
    <p>Go a week with us for an internship intensive within a framework of holidays. A total immersion in the meals, musical evenings and dance</p>
  </div>
</section>

<section class="featured">
  <div class="featured-copy abs">
    <h2>FEATURED VIDEO</h2>
    <p>Go a week with us for an internship intensive within a framework of holidays. A total immersion in the work of actor mixing fun: swimming, improvisation games, meals, musical evenings and dance ... with the private coaching, casting preparation day photo shoot and PRO images for your demo tape.</p>
    <p>Go a week with us for an internship intensive within a framework of holidays. A total immersion in the work of actor mixing fun: swimming, improvisation games, meals, musical evenings and dance ...</p>
  </div>
  <div class="btn-outline abs">WATCH VIDEO</div>
  <div class="video-still abs" role="img" aria-label="Video still of actors sitting on the floor of a living room during a rehearsal"></div>
  <div class="play abs"><svg width="30" height="32" viewBox="0 0 30 32"><path d="M6 3l22 13L6 29z" fill="#fff"/></svg></div>
</section>

<section class="gallery">
  <h2 class="section-title abs center-x" style="left:600px;top:38px">PHOTO GALLERY</h2>
  <div class="filters abs">
    <span class="on">ALL</span><span class="sep">|</span><span>COACHING</span><span class="sep">|</span><span>LIEU</span><span class="sep">|</span><span>SOIREES NETWORKING</span><span class="sep">|</span><span>STAGES</span>
  </div>
  <div class="tile" style="left:84px;top:164px;width:511px;height:204px;background:linear-gradient(135deg,#5a3a22,#9a6a3a 55%,#c89050)" role="img" aria-label="Group photo of actors posing around a vintage car among autumn leaves"></div>
  <div class="tile" style="left:603px;top:164px;width:251px;height:418px;background:linear-gradient(160deg,#2a2420,#4a3e34 50%,#1e1a16)" role="img" aria-label="Close-up of a film clapperboard"></div>
  <div class="tile" style="left:864px;top:164px;width:249px;height:204px;background:linear-gradient(135deg,#3a3128,#7a6a58 60%,#b8a890)" role="img" aria-label="Sepia photo of actors rehearsing indoors"></div>
  <div class="tile tile-stages" style="left:84px;top:378px;width:249px;height:204px">
    <h4>STAGES</h4>
    <p>Dans une situation extrême, elle m'a non seulement rassurée fait travailler elle m'a amenée ailleurs</p>
    <div class="zoom"><svg width="14" height="14" viewBox="0 0 14 14"><circle cx="6" cy="6" r="4" fill="none" stroke="#2f8bd3" stroke-width="2"/><path d="M9 9l4 4" stroke="#2f8bd3" stroke-width="2"/></svg></div>
  </div>
  <div class="tile" style="left:344px;top:378px;width:251px;height:204px;background:linear-gradient(135deg,#3a2c20,#7a5e40 50%,#b89a70)" role="img" aria-label="Photo of a coaching session in a warm-lit room"></div>
  <div class="tile" style="left:864px;top:378px;width:249px;height:204px;background:linear-gradient(180deg,#4a6a30,#7aa048 55%,#8cb458)" role="img" aria-label="Photo of a workshop group seated on a park lawn"></div>
</section>

<section class="testimonial" role="region" aria-label="Testimonials">
  <h2 class="abs center-x">WE COMEDIEN (NE) S PARLENT DE ATELIER QUAI SEPT</h2>
  <div class="quote-badge abs"><svg width="28" height="22" viewBox="0 0 28 22" fill="#2b2824"><path d="M0 22V12C0 5 4 1 11 0v4C7 5 5 8 5 11h6v11zM16 22V12c0-7 4-11 11-12v4c-4 1-6 4-6 7h6v11z"/></svg></div>
  <svg class="chev abs" style="left:132px" width="22" height="116" viewBox="0 0 22 116"><path d="M20 2L2 58l18 56" fill="none" stroke="#d8d8d8" stroke-width="2"/></svg>
  <svg class="chev abs" style="left:1044px" width="22" height="116" viewBox="0 0 22 116"><path d="M2 2l18 56L2 114" fill="none" stroke="#d8d8d8" stroke-width="2"/></svg>
  <p class="quote-text abs center-x">J'ai rencontré Ninon en occasion of a tournage où je devais interpréter a personnage dans une situation extrême, elle m'a non seulement rassurée, fait travailler, plus elle m'a amenée ailleurs ... c'est une observatrice pointilleuse. J'ai rencontré Ninon on the occasion on travailler, plus elle m'a amenée ailleurs ... c'est une observatrice pointilleuse.</p>
  <div class="stars abs center-x">
    <svg width="16" height="15" viewBox="0 0 16 15"><path d="M8 1l2 5h5l-4 3 1.5 5L8 11l-4.5 3L5 9 1 6h5z" fill="none" stroke="#e7b521" stroke-width="1.3"/></svg>
    <svg width="16" height="15" viewBox="0 0 16 15"><path d="M8 1l2 5h5l-4 3 1.5 5L8 11l-4.5 3L5 9 1 6h5z" fill="none" stroke="#e7b521" stroke-width="1.3"/></svg>
    <svg width="16" height="15" viewBox="0 0 16 15"><path d="M8 1l2 5h5l-4 3 1.5 5L8 11l-4.5 3L5 9 1 6h5z" fill="none" stroke="#e7b521" stroke-width="1.3"/></svg>
    <svg width="16" height="15" viewBox="0 0 16 15"><path d="M8 1l2 5h5l-4 3 1.5 5L8 11l-4.5 3L5 9 1 6h5z" fill="none" stroke="#e7b521" stroke-width="1.3"/></svg>
    <svg width="16" height="15" viewBox="0 0 16 15"><path d="M8 1l2 5h5l-4 3 1.5 5L8 11l-4.5 3L5 9 1 6h5z" fill="#e7b521"/></svg>
  </div>
  <div class="quote-name abs center-x">Name : Claire DUMONT</div>
</section>

<section class="contact">
  <h2 class="section-title abs center-x" style="left:600px;top:36px">CONTACT US</h2>
  <p class="lead abs center-x" style="left:600px;top:76px;width:800px">Go a week with us for an internship intensive within a framework of holidays. A total immersion in the work of actor mixing</p>
  <div class="map abs" role="img" aria-label="Street map of central Paris with a location pin"></div>
  <p class="contact-copy abs">Go a week with us for an internship intensive within a framework of holidays. A total immersion in the work of actor mixing fun: games, meals, musical evenings and dance shoot and PRO images for your demo tape.</p>

  <div class="abs" style="left:622px;top:235px">
    <div class="contact-label">ADDRESS</div>
    <div class="contact-detail" style="margin-top:10px"># 2547 Lorem Ipsum Dummy<br>Lorem Ipsum Dummy</div>
  </div>
  <div class="abs" style="left:622px;top:342px">
    <div class="contact-label">PHONE</div>
    <div class="contact-detail" style="margin-top:10px">Mobile : +33 6 12 48 30 57</div>
  </div>
  <div class="abs" style="left:873px;top:235px">
    <div class="contact-label">EMAIL ADDRESS</div>
    <div class="contact-detail" style="margin-top:10px">General : contact@atelier-quai-sept.example<br>Office : office@studio-mail.example</div>
  </div>
  <div class="contact-label abs" style="left:873px;top:326px">FOLLOW US</div>
  <div class="socials abs"><span></span><span></span><span></span><span></span><span></span></div>
</section>

<footer class="site-footer">
  <div class="copy abs center-x">© Copyright 2016. Atelier Quai Sept All Rights Reserved</div>
  <div class="code abs">C2</div>
</footer>

</body>
</html>
```